Business card design for my company.
I would like the card's background colour to be black. You can also see our web site to get an idea of our brand. https://www.tmwhomecrafting.com.au/
- Name
- Email

```html
<!DOCTYPE html>
<html lang="en">
<head>
<meta charset="utf-8">
<title>TMW Home Crafting – Business Card</title>
<link href="https://fonts.googleapis.com/css2?family=Exo+2:wght@600;700&family=Tinos&display=swap" rel="stylesheet">
<style>
  :root {
    --navy: #252a3a;
    --green: #0b9245;
    --paper: #ffffff;
    --backdrop: #e6e6e6;
    --ink: #222633;
  }
  * { margin: 0; padding: 0; box-sizing: border-box; }
  html, body { width: 1200px; height: 849px; overflow: hidden; }
  body {
    background: var(--backdrop);
    display: flex;
    flex-direction: column;
    align-items: center;
    justify-content: center;
    gap: 40px;
  }
  .card {
    position: relative;
    width: 600px;
    height: 344px;
    overflow: hidden;
  }
  .card-bands {
    position: absolute;
    inset: 0;
    width: 100%;
    height: 100%;
  }
  /* Front */
  .card-front { background: var(--navy); }
  .brand-name {
    position: absolute;
    left: 0; right: 0;
    top: 118px;
    text-align: center;
    font-family: "Exo 2", sans-serif;
    font-weight: 700;
    font-size: 40px;
    letter-spacing: 1px;
    color: var(--paper);
  }
  /* Back */
  .card-back { background: var(--paper); }
  .person {
    position: absolute;
    left: 30px;
    top: 50px;
    font-family: "Exo 2", sans-serif;
    color: var(--green);
  }
  .person-name {
    font-weight: 700;
    font-size: 25px;
    line-height: 1;
    text-decoration: underline;
    text-decoration-thickness: 2px;
    text-underline-offset: 3px;
  }
  .person-title {
    font-weight: 600;
    font-size: 13px;
    margin-top: 3px;
  }
  .contact-list {
    position: absolute;
    left: 54px;
    top: 132px;
    list-style: none;
  }
  .contact-item {
    display: flex;
    align-items: center;
    gap: 9px;
    height: 39.5px;
    font-family: "Tinos", serif;
    font-size: 17px;
    color: var(--ink);
  }
  .contact-icon { width: 31px; height: 31px; flex: none; }
</style>
</head>
<body>

  <section class="card card-front" aria-label="Card front">
    <svg class="card-bands" viewBox="0 0 688 394" preserveAspectRatio="none" aria-hidden="true">
      <rect x="0" y="342" width="688" height="52" fill="var(--green)"/>
      <polygon points="216,342 429,342 476,394 261,394" fill="var(--navy)"/>
    </svg>
    <div class="brand-name">TMW Home Crafting</div>
  </section>

  <section class="card card-back" aria-label="Card back">
    <svg class="card-bands" viewBox="0 0 688 394" preserveAspectRatio="none" aria-hidden="true">
      <polygon points="384,72 688,72 688,122 297,122" fill="var(--green)"/>
      <polygon points="410,122 688,122 688,160 473,160" fill="var(--navy)"/>
    </svg>

    <div class="person">
      <div class="person-name">Liam Ashford</div>
      <div class="person-title">General Manager</div>
    </div>

    <ul class="contact-list">
      <li class="contact-item">
        <svg class="contact-icon" viewBox="0 0 32 32" aria-hidden="true">
          <circle cx="16" cy="16" r="16" fill="var(--navy)"/>
          <path d="M11.5 9.5l2.5-.5 1.6 3.4-1.7 1.2c.8 1.8 2.2 3.2 4 4l1.2-1.7 3.4 1.6-.5 2.5c-.2.8-1 1.2-1.8 1-5-1.2-8.9-5.1-10-10.1-.2-.8.3-1.5 1.3-1.4z" fill="#fff"/>
        </svg>
        <span>0400 123 456</span>
      </li>
      <li class="contact-item">
        <svg class="contact-icon" viewBox="0 0 32 32" aria-hidden="true">
          <circle cx="16" cy="16" r="16" fill="var(--navy)"/>
          <rect x="9" y="11" width="14" height="10" fill="none" stroke="#fff" stroke-width="1.4"/>
          <path d="M9 11l7 6 7-6" fill="none" stroke="#fff" stroke-width="1.4"/>
        </svg>
        <span>info@tmwhomecrafting.com.au</span>
      </li>
      <li class="contact-item">
        <svg class="contact-icon" viewBox="0 0 32 32" aria-hidden="true">
          <circle cx="16" cy="16" r="16" fill="var(--navy)"/>
          <g fill="none" stroke="#fff" stroke-width="1.1">
            <circle cx="16" cy="16" r="7"/>
            <ellipse cx="16" cy="16" rx="3" ry="7"/>
            <path d="M9 16h14M10 12.5h12M10 19.5h12"/>
          </g>
        </svg>
        <span>tmwhomecrafting.com.au</span>
      </li>
      <li class="contact-item">
        <svg class="contact-icon" viewBox="0 0 32 32" aria-hidden="true">
          <circle cx="16" cy="16" r="16" fill="var(--navy)"/>
          <path d="M16 8c-3.3 0-6 2.6-6 5.9 0 4.3 6 10.1 6 10.1s6-5.8 6-10.1C22 10.6 19.3 8 16 8z" fill="#fff"/>
          <circle cx="16" cy="14" r="2.3" fill="var(--navy)"/>
        </svg>
        <span>Launceston, Tasmania, Australia</span>
      </li>
    </ul>
  </section>

</body>
</html>
```